Vantoq Business Card Project showing the logo and a marbo image on the rear

Design a whacky but professional business card, the logo is for the front and the Marbo image is for the rear. Happy to consider other open source Marbo Images if the designer wants to select one from the web. Vantoq is a competitor to OMB.com.au and Pellory.com.au and is based around every property in Australia

Target Market(s)

Business

Contact Information for Business Card

Name, Title, Email, Web, Phone Number

Font styles to use
Other font styles liked:
• avenir

Requirements
Must have
• Image on Back logo on front
Nice to have
• Happy to consider other images on rear, preftably Colin Marbo. Image supplied I own, we can use open source other Marbo Images

```html
<!DOCTYPE html>
<html lang="en">
<head>
<meta charset="utf-8">
<title>Vantoq Business Card</title>
<link href="https://fonts.googleapis.com/css2?family=Nunito+Sans:wght@400;600;800&display=swap" rel="stylesheet">
<style>
  :root {
    --stage: #e4e4e4;
    --card: #fbfbfb;
    --ink: #111111;
    --accent: #f7931e;
    --rule: #b9b9b9;
    --sky: #2f8fe0;
    --shadow: rgba(0,0,0,0.18);
  }
  * { box-sizing: border-box; margin: 0; padding: 0; }
  html, body { width: 1200px; height: 930px; overflow: hidden; }
  body {
    background: var(--stage);
    font-family: "Nunito Sans", "Avenir", sans-serif;
    display: flex;
    align-items: center;
    justify-content: center;
    gap: 60px;
  }
  .card {
    width: 540px;
    height: 309px;
    border-radius: 3px;
    box-shadow: 0 10px 26px var(--shadow);
    position: relative;
    overflow: hidden;
  }
  .card--front { background: var(--card); color: var(--ink); }

  .brand {
    position: absolute;
    top: 70px;
    left: 190px;
    display: flex;
    align-items: center;
    gap: 14px;
  }
  .brand__mark { width: 30px; height: 30px; background: var(--accent); }
  .brand__name { font-weight: 800; font-size: 52px; letter-spacing: 1px; line-height: 1; }

  .person {
    position: absolute;
    top: 190px;
    left: 40px;
    width: 190px;
    text-align: right;
  }
  .person__name { color: var(--accent); font-weight: 600; font-size: 20px; line-height: 1.2; }
  .person__title { font-size: 13px; margin-top: 2px; }

  .divider {
    position: absolute;
    top: 180px;
    left: 250px;
    width: 1px;
    height: 78px;
    background: var(--rule);
  }

  .contact {
    position: absolute;
    top: 186px;
    left: 270px;
    list-style: none;
    font-size: 14px;
    line-height: 1.55;
  }
  .contact__item { display: flex; align-items: center; gap: 8px; }
  .contact__icon { width: 13px; height: 13px; flex: none; }
  .contact__highlight { color: var(--accent); }

  .card--back {
    background: linear-gradient(180deg, var(--sky) 0%, #3a7fd8 28%, #e8672a 55%, #f2a21e 70%, #3e8f3a 85%, #6e6e6e 100%);
  }
</style>
</head>
<body>
  <section class="card card--front" aria-label="Card front">
    <div class="brand">
      <span class="brand__mark"></span>
      <span class="brand__name">Vantoq</span>
    </div>

    <div class="person">
      <p class="person__name">Daniel Ashford</p>
      <p class="person__title">Managing Director</p>
    </div>

    <div class="divider"></div>

    <ul class="contact">
      <li class="contact__item">
        <svg class="contact__icon" viewBox="0 0 24 24"><path fill="#f7931e" d="M6.6 10.8a15.1 15.1 0 0 0 6.6 6.6l2.2-2.2c.3-.3.7-.4 1-.2 1.1.4 2.3.6 3.6.6.6 0 1 .4 1 1V20c0 .6-.4 1-1 1A17 17 0 0 1 3 4c0-.6.4-1 1-1h3.5c.6 0 1 .4 1 1 0 1.3.2 2.5.6 3.6.1.3 0 .7-.2 1z"/></svg>
        <span>044-987 654 321</span>
      </li>
      <li class="contact__item">
        <svg class="contact__icon" viewBox="0 0 24 24"><rect x="2" y="5" width="20" height="14" fill="#f7931e"/><path d="M2 5l10 8 10-8" fill="none" stroke="#fff" stroke-width="2"/></svg>
        <span>hello@vantoq.com</span>
      </li>
      <li class="contact__item">
        <svg class="contact__icon" viewBox="0 0 24 24"><circle cx="12" cy="12" r="10" fill="#f7931e"/><path d="M2 12h20M12 2c3 3 3 17 0 20M12 2c-3 3-3 17 0 20" fill="none" stroke="#fff" stroke-width="1.5"/></svg>
        <span>www.<span class="contact__highlight">vantoq</span>.com</span>
      </li>
    </ul>
  </section>

  <section class="card card--back" role="img" aria-label="Colourful naive-style painting of a crowded city skyline with bright buildings under a blue sky"></section>
</body>
</html>
```